Creative, fresh business card design for Ripplecraft Facades

We need a fresh, creative business card design for Ripplecraft Facades. We are the manufacturer of Ripplecraft Facades in Australia. Wall panels are 2400 x 1200mm panels made from MDF and feature 3D patterns on the face of the panel. The colours to be used are green, silver/grey and white RGB
Red 187
Green 207
Blue 65.

An idea is to possibly use a watermark of one of our designs as a background (like on the "Grids" design on the left hand side of page 2 of our brochure).

Target Market(s)

Interior designers, architects, builders and home renovators

Industry/Entity Type

Business

Contact Information for Business Card

Details to go on the card are:
Our logo (attached),
Slogan: "Decorative panels for interiors and exteriors",
Contact name,
Position,
Mobile phone number,
Business address,
Business phone,
Business fax,
Website and
Email address.

I have attached a few images of our panels and our brochure for reference.

The colours of the business card should feature our logo colours which are: RGB
Red 187
Green 207
Blue 65

Requirements
Must have
• Very modern fonts and design. Some of the designs shown especially the "Prisms" design which is a popular design.
Nice to have
• Creative but simple design. Very contemporary.
Should not have
• Anything ornate or old fashioned.

```html
<!DOCTYPE html>
<html lang="en">
<head>
<meta charset="utf-8">
<title>Ripplecraft Facades – Business Card</title>
<link rel="stylesheet" href="https://fonts.googleapis.com/css2?family=Arimo:wght@400;700&display=swap">
<style>
  :root {
    --brand-green: #bbcf41;
    --brand-grey: #8e9094;
    --ink: #3a3a3a;
    --ink-soft: #6b6d70;
    --paper: #ffffff;
    --backdrop: #e6e4e1;
    --rule: #5d6a73;
  }
  * { box-sizing: border-box; margin: 0; padding: 0; }
  html, body { width: 1200px; height: 987px; overflow: hidden; }
  body {
    background: var(--backdrop);
    font-family: "Arimo", Arial, sans-serif;
    position: relative;
  }
  .card {
    position: absolute;
    left: 293px;
    width: 615px;
    height: 350px;
    box-shadow: 0 2px 6px rgba(0,0,0,0.25);
    overflow: hidden;
  }
  .card--front { top: 130px; background: var(--paper); }
  .card--back { top: 506px; background: var(--brand-grey); }

  /* brand name block */
  .brand {
    position: absolute;
    display: flex;
    align-items: center;
    gap: 10px;
  }
  .brand__square { width: 22px; height: 22px; background: var(--brand-green); flex: none; }
  .brand__name {
    font-weight: 700;
    font-size: 27px;
    color: var(--brand-green);
    white-space: nowrap;
    line-height: 1;
  }
  .tagline {
    position: absolute;
    font-size: 12.5px;
    letter-spacing: 2.6px;
    line-height: 17px;
  }

  .card--front .brand { right: 34px; top: 40px; flex-direction: row; }
  .card--front .brand__name { font-size: 26px; }
  .card--front .tagline {
    right: 34px; top: 110px; text-align: right; color: var(--ink-soft);
  }

  .name-marker {
    position: absolute; left: 0; top: 184px; width: 9px; height: 45px;
    background: var(--brand-grey);
  }
  .person__name {
    position: absolute; left: 30px; top: 182px;
    font-weight: 700; font-size: 23px; letter-spacing: 0.5px;
    color: var(--brand-green);
  }
  .person__role {
    position: absolute; left: 30px; top: 212px;
    font-size: 17px; color: var(--ink-soft);
  }
  .divider {
    position: absolute; left: 30px; right: 35px; top: 239px;
    height: 1px; background: var(--rule);
  }

  .contact-list {
    position: absolute; left: 30px; top: 250px; list-style: none;
  }
  .contact-list li {
    display: flex; align-items: center; gap: 9px;
    height: 23.5px; font-size: 16.5px; color: var(--ink);
  }
  .contact-list svg { width: 15px; height: 15px; flex: none; }

  .address {
    position: absolute; right: 35px; top: 250px;
    text-align: right; font-style: normal;
    font-size: 16.5px; line-height: 23.5px; color: var(--ink);
  }
  .address .web { letter-spacing: 1.4px; }

  .footer-band {
    position: absolute; left: 0; bottom: 0; width: 100%; height: 15px;
  }

  .card--back .brand {
    left: 0; right: 0; top: 118px; justify-content: center;
  }
  .card--back .brand__name { font-size: 30px; }
  .card--back .tagline {
    left: 0; right: 0; top: 228px; text-align: center; color: var(--paper);
  }
</style>
</head>
<body>

<section class="card card--front" aria-label="Business card front">
  <div class="brand">
    <span class="brand__square"></span>
    <span class="brand__name">Ripplecraft Facades</span>
  </div>
  <p class="tagline">decorative panels for<br>interiors &amp; landscapes</p>

  <span class="name-marker"></span>
  <h1 class="person__name">OWEN PRITCHARD</h1>
  <p class="person__role">CEO&amp;Founder</p>
  <span class="divider"></span>

  <ul class="contact-list">
    <li>
      <svg viewBox="0 0 16 16" aria-hidden="true"><path fill="#bbcf41" d="M3.2 1.5l2.3-.3 1.4 3.3-1.5 1.2c.8 1.8 2.1 3.1 3.9 3.9l1.2-1.5 3.3 1.4-.3 2.3c-.2 1-1 1.7-2 1.6C6.4 13 3 9.6 2.6 4.5c-.1-1 .6-1.8 1.6-2z"/></svg>
      <span>(03) 5221 7804</span>
    </li>
    <li>
      <svg viewBox="0 0 16 16" aria-hidden="true"><path fill="#bbcf41" d="M4 1h7l1 2v3H4zM1 6h14v6h-2v3H3v-3H1zm4 4v3h6v-3z"/></svg>
      <span>(03) 5221 7805</span>
    </li>
    <li>
      <svg viewBox="0 0 16 16" aria-hidden="true"><path fill="#bbcf41" d="M1 3h14v10H1zm1.5 1.3v.4L8 8.6l5.5-3.9v-.4z"/></svg>
      <span>opritchard@ripplecraft.com</span>
    </li>
  </ul>

  <address class="address">
    42 Tamarind Crescent<br>
    Geelong, Victoria 3220<br>
    <span class="web">www.ripplecraft.com</span>
  </address>

  <svg class="footer-band" viewBox="0 0 615 15" preserveAspectRatio="none" aria-hidden="true">
    <polygon points="0,0 403,0 399,15 0,15" fill="#bbcf41"/>
    <polygon points="407,0 615,0 615,15 403,15" fill="#8e9094"/>
  </svg>
</section>

<section class="card card--back" aria-label="Business card back">
  <div class="brand">
    <span class="brand__square"></span>
    <span class="brand__name">Ripplecraft Facades</span>
  </div>
  <p class="tagline">decorative panels for<br>interiors &amp; landscapes</p>
</section>

</body>
</html>
```